jQuery Mobile CSS for web app

Task Outline:
Create jQuery Mobile themeroller compliant CSS and icons for a mobile web app.
Task Description:
Brindle Solutions are in the process of implementing a new, web based version of their Tessel operations platform.
The web based version of Tessel is built on top of the jQuery Mobile platform and we are looking for a designer to create a jQuery Mobile themeroller compliant CSS theme pack that we can plug into our application. The aim is to remove the standard jQuery Mobile look and feel and to introduce the Brindle branding throughout the new web app.
A number of screenshots are shown in the attached design spec (brindle_solutions.pdf) that show what the current (Windows Mobile 6.5) application looks like, alongside the development version of our new web app.
Deliverables:
• jQuery Mobile (v 1.4.2) themeroller compliant CSS which provides theming for all jQuery Mobile UI components.
• Example html showing how to use the CSS theme (especially where additional html/css classes are required).
• New set of status icons (as listed in attachment)
Inspiration:
See our website for current branding: www.brindle-solutions-demo.net

```html
<!DOCTYPE html>
<html lang="en">
<head>
<meta charset="utf-8">
<title>Brindle – Job Header Details</title>
<link href="https://fonts.googleapis.com/css2?family=Open+Sans:wght@400;600&display=swap" rel="stylesheet">
<style>
  :root {
    --page-bg: #1c1c1c;
    --header-top: #3b3b3b;
    --header-bottom: #1f1f1f;
    --divider: #2c2c2c;
    --divider-light: #3a3a3a;
    --label: #a9a9a9;
    --field-bg: #ffffff;
    --field-border: #d6d6d6;
    --field-text: #5a5a5a;
    --chevron: #7a7a7a;
    --white: #ffffff;
    --nav-active-top: #d9d9d9;
    --nav-active-bottom: #b9b9b9;
    --nav-top: #2e2e2e;
    --nav-bottom: #1a1a1a;
    --icon-muted: #9a9a9a;
    --icon-dark: #111111;
  }
  * { box-sizing: border-box; margin: 0; padding: 0; }
  html, body {
    width: 830px; height: 1200px; overflow: hidden;
    background: var(--page-bg);
    font-family: "Open Sans", Arial, sans-serif;
  }
  .app {
    position: relative; width: 830px; height: 1200px;
    background: var(--page-bg);
  }

  /* Header bar */
  .app-header {
    position: absolute; top: 0; left: 0; width: 830px; height: 120px;
    background: linear-gradient(var(--header-top), var(--header-bottom));
    border-bottom: 2px solid var(--divider);
  }
  .brand {
    position: absolute; left: 38px; top: 26px;
    display: flex; align-items: center; gap: 10px;
    color: var(--white); font-size: 44px; font-weight: 600; letter-spacing: 0.5px;
  }
  .brand-dot { width: 12px; height: 12px; border-radius: 50%; background: var(--white); }
  .header-divider {
    position: absolute; top: 26px; width: 1px; height: 68px; background: var(--divider-light);
  }
  .header-divider.left { left: 277px; }
  .header-divider.right { left: 729px; }
  .page-title {
    position: absolute; left: 315px; top: 46px;
    color: var(--white); font-size: 19px; font-weight: 400; letter-spacing: 0.3px;
  }
  .menu-button { position: absolute; left: 763px; top: 44px; width: 36px; height: 34px; }
  .menu-button span {
    position: absolute; left: 0; width: 36px; height: 4px; background: var(--white);
  }
  .menu-button span:nth-child(1) { top: 0; }
  .menu-button span:nth-child(2) { top: 15px; }
  .menu-button span:nth-child(3) { top: 30px; }

  /* Form */
  .job-form { position: absolute; top: 122px; left: 0; width: 830px; }
  .form-field {
    height: 226px; padding: 44px 50px 0 50px;
    border-bottom: 2px solid var(--divider);
  }
  .field-label {
    display: block; height: 30px; line-height: 30px;
    color: var(--label); font-size: 25px; font-weight: 400;
    margin-bottom: 28px;
  }
  .field-input {
    position: relative; width: 729px; height: 69px;
    background: var(--field-bg); border: 1px solid var(--field-border); border-radius: 5px;
    padding-left: 26px; line-height: 67px;
    color: var(--field-text); font-size: 22px;
  }
  .field-select .chevron { position: absolute; right: 20px; top: 24px; }

  /* Bottom navigation */
  .nav-bar {
    position: absolute; left: 0; top: 1083px; width: 830px; height: 117px;
    display: flex; gap: 3px; background: #0e0e0e;
  }
  .nav-button {
    position: relative; flex: 1; height: 117px;
    background: linear-gradient(var(--nav-top), var(--nav-bottom));
    display: flex; align-items: center; justify-content: center;
  }
  .nav-button.is-active { background: linear-gradient(var(--nav-active-top), var(--nav-active-bottom)); }
  .nav-code {
    position: absolute; right: 34px; top: 52px;
    color: var(--white); font-size: 18px;
  }
</style>
</head>
<body>
<div class="app">
  <header class="app-header">
    <div class="brand"><span>Brindle</span><span class="brand-dot"></span></div>
    <div class="header-divider left"></div>
    <h1 class="page-title">JOB HEADER D...</h1>
    <div class="header-divider right"></div>
    <div class="menu-button" aria-label="Menu"><span></span><span></span><span></span></div>
  </header>

  <form class="job-form">
    <div class="form-field">
      <label class="field-label">Customer Name</label>
      <div class="field-input field-select">One
        <svg class="chevron" width="26" height="18" viewBox="0 0 26 18"><polyline points="3,4 13,14 23,4" fill="none" stroke="var(--chevron)" stroke-width="4"/></svg>
      </div>
    </div>
    <div class="form-field">
      <label class="field-label">Customer Reference</label>
      <div class="field-input">Two</div>
    </div>
    <div class="form-field">
      <label class="field-label">Job Discription</label>
      <div class="field-input">Three</div>
    </div>
  </form>

  <nav class="nav-bar">
    <div class="nav-button is-active" aria-label="Back">
      <svg width="72" height="48" viewBox="0 0 72 48">
        <path d="M20 10 L4 18 L20 26" fill="none" stroke="var(--icon-dark)" stroke-width="5" stroke-linejoin="miter"/>
        <path d="M6 18 H52 a12 12 0 0 1 0 24 H20" fill="none" stroke="var(--icon-dark)" stroke-width="5"/>
      </svg>
    </div>
    <div class="nav-button" aria-label="Home">
      <svg width="80" height="44" viewBox="0 0 80 44">
        <path d="M4 36 V24 L40 6 L76 24 V36 Z" fill="none" stroke="var(--icon-muted)" stroke-width="4" stroke-linejoin="round"/>
      </svg>
    </div>
    <div class="nav-button" aria-label="Forward">
      <svg width="72" height="48" viewBox="0 0 72 48">
        <path d="M66 18 H20 a12 12 0 0 0 0 24 H50" fill="none" stroke="var(--icon-muted)" stroke-width="5"/>
        <path d="M52 8 L68 18 L52 28 Z" fill="var(--icon-muted)"/>
      </svg>
      <span class="nav-code">C8</span>
    </div>
  </nav>
</div>
</body>
</html>
```